Business Card Design (NEW FILES)

ATTENTION: New vector files are available. Please update your design to reflect/use the new (better resolution) logo images.

Seeking a unique and professional business card design for a commercial drone photography/videography business. The layout should feature
the logo (attached) and include the following information:
Owen Tarrick
614-502-7738
www.skylarkreelworks.example
NRD Certified Remote Pilot

Owen Tarrick

```html
<!DOCTYPE html>
<html lang="en">
<head>
<meta charset="utf-8">
<title>Skylark Reelworks – Business Card</title>
<link rel="stylesheet" href="https://fonts.googleapis.com/css2?family=Arimo:wght@400;700&display=swap">
<style>
  :root {
    --navy: #12173d;
    --orange: #e9804a;
    --white: #ffffff;
    --backdrop: #1c1c1e;
  }
  * { box-sizing: border-box; margin: 0; padding: 0; }
  html, body {
    width: 1200px;
    height: 963px;
    overflow: hidden;
    background: var(--backdrop);
    font-family: "Arimo", Arial, sans-serif;
  }
  .sheet {
    position: relative;
    width: 1200px;
    height: 963px;
  }
  .card {
    position: absolute;
    left: 215px;
    width: 770px;
    height: 440px;
    border-radius: 34px;
    overflow: hidden;
  }
  .card--front { top: 28px; background: var(--white); color: var(--navy); }
  .card--back { top: 495px; }

  /* front */
  .holder {
    position: absolute;
    left: 62px;
    top: 140px;
  }
  .holder__name {
    font-weight: 700;
    font-size: 28px;
    letter-spacing: 0.5px;
    text-transform: uppercase;
    line-height: 1.1;
  }
  .holder__name .surname { color: var(--orange); }
  .holder__role {
    font-size: 20px;
    margin-top: 2px;
  }
  .divider {
    position: absolute;
    left: 62px;
    right: 90px;
    top: 214px;
    height: 2px;
    background: var(--navy);
  }
  .contact {
    position: absolute;
    left: 62px;
    top: 238px;
    list-style: none;
    font-size: 20px;
  }
  .contact li {
    display: flex;
    align-items: center;
    gap: 14px;
    margin-bottom: 14px;
  }
  .contact svg { width: 18px; height: 18px; flex: none; }

  .brand {
    position: absolute;
    right: 90px;
    top: 78px;
    display: flex;
    align-items: center;
    gap: 14px;
    color: var(--navy);
    font-size: 32px;
    font-weight: 400;
    line-height: 1.05;
    text-transform: uppercase;
    letter-spacing: 1px;
  }
  .brand__dot {
    width: 26px;
    height: 26px;
    border-radius: 50%;
    background: var(--navy);
    flex: none;
  }
  .credentials {
    position: absolute;
    right: 90px;
    top: 312px;
    text-align: right;
    font-size: 22px;
    line-height: 1.45;
  }

  /* back */
  .back-art {
    position: absolute;
    inset: 0;
    background: linear-gradient(200deg, var(--navy) 0%, var(--navy) 46%, var(--orange) 46%, var(--orange) 100%);
  }
  .card--back .brand {
    color: var(--white);
    top: 34px;
    right: 48px;
    font-size: 26px;
  }
  .card--back .brand__dot { background: var(--white); width: 22px; height: 22px; }
</style>
</head>
<body>
<main class="sheet">
  <section class="card card--front" aria-label="Business card front">
    <div class="holder">
      <p class="holder__name">Owen <span class="surname">Tarrick</span></p>
      <p class="holder__role">Owner</p>
    </div>
    <div class="brand"><span class="brand__dot"></span><span>Skylark<br>Reelworks</span></div>
    <div class="divider"></div>
    <ul class="contact">
      <li>
        <svg viewBox="0 0 20 20" aria-hidden="true"><path d="M5 2l3 4-2 2a11 11 0 0 0 6 6l2-2 4 3-2 3C9 18 2 11 2 4z" fill="var(--orange)"/></svg>
        <span>614-502-7738</span>
      </li>
      <li>
        <svg viewBox="0 0 20 20" aria-hidden="true"><g fill="none" stroke="var(--orange)" stroke-width="1.6"><circle cx="10" cy="10" r="8"/><ellipse cx="10" cy="10" rx="3.5" ry="8"/><path d="M2 10h16M4 5.5h12M4 14.5h12"/></g></svg>
        <span>www.skylarkreelworks.example</span>
      </li>
    </ul>
    <p class="credentials">NRD Certified Remote Pilot<br>Fully Insured</p>
  </section>

  <section class="card card--back" aria-label="Business card back">
    <div class="back-art" role="img" aria-label="Large drone and camera illustration in navy and orange"></div>
    <div class="brand"><span class="brand__dot"></span><span>Skylark Reelworks</span></div>
  </section>
</main>
</body>
</html>
```